Verpackungen für Parfum-Proben
Besten Dank! Das Team ist begeistert - also bin ich es auch und wir freuen uns schon, unsere Parfum Proben in Zukunft in diesem tollen Design weitergeben zu können! Danke!
Zielgruppe
Hallo allerseits! Wir sind im Direktvertrieb in den Bereichen Parfum & Kosmetik tätig.
Aufgabenstellung
Für unsere Parfum-Proben benötige ich ein ansprechendes, modernes Design.
Das Design muss relativ neutral gehalten werden, da die Blister sowohl für Herren- als auch Damenproben verwendet werden.
Auf Vorder- und Rückseite soll unser Team-Logo (NaseNomade®) sichtbar sein (Vorderseite größer, Rückseite kleiner).
Auf der linken Innenseite sollte Plätz für einen netten Spruch (den ich mir noch überlege) sein.
Auf der Rückseite muss Platz (weißes / helles Feld) für einen Stempel und/oder Aufkleber (Kontaktdaten des Distributors) sein.
Unser Logo ist Lila - Das farbliche Design sollte dazu passen.
Bei Fragen, einfach Nachricht :)
Daten:
Endformat: 133 x 74 mm
Datenformat: 139 x 80 mm
1-teilig, gestanzt, genutet, einseitig geklebt geliefert
Bitte verwenden Sie für positive Schriftstärken mindestens 9pt (ca. 3,17mm) und bei negativen Schriftstärken mindestens 13pt (ca. 4,59mm).
Abmessungen / Druck- / Designvorlage, Logo, etc.: https://dateiwolke-beispiel.de/ordner/X7pLrT2k#v9wQe4nZb6Hs1Ym_d8cKfa

```html
<!DOCTYPE html>
<html lang="de">
<head>
<meta charset="utf-8">
<title>NaseNomade – Probenblister Druckbogen</title>
<link rel="stylesheet" href="https://fonts.googleapis.com/css2?family=Open+Sans:wght@400&display=swap">
<style>
  :root {
    --canvas: #ffffff;
    --brand-purple: #6b54ad;
    --mist-light: #eceef9;
    --mist-mid: #c9cbeb;
    --mist-deep: #9a9fd6;
    --bottle-blue: #3a4ea8;
    --bottle-violet: #5b3d8e;
    --night: #14102e;
    --nebula-violet: #4a2a86;
    --nebula-magenta: #c02a9a;
    --nebula-pink: #e88fd6;
    --nebula-glow: #f3e6f6;
    --text-light: #ffffff;
    --text-dark: #1a1a1a;
    --fold: #ffffff;
  }
  * { box-sizing: border-box; margin: 0; padding: 0; }
  html, body {
    width: 1200px; height: 890px; overflow: hidden;
    background: var(--canvas);
    font-family: "Open Sans", sans-serif;
  }
  .print-sheet {
    position: absolute; left: 221px; top: 16px;
    width: 759px; height: 857px;
    display: grid;
    grid-template-columns: 378px 378px;
    grid-template-rows: 421px 421px;
    column-gap: 3px; row-gap: 15px;
  }
  .panel { position: relative; overflow: hidden; }
  .panel-media { position: absolute; inset: 0; }

  .brand-name {
    position: absolute;
    color: var(--brand-purple);
    font-family: "Open Sans", sans-serif;
    font-weight: 400;
    letter-spacing: 0.5px;
    white-space: nowrap;
  }

  /* Rückseite */
  .back-cover .panel-media {
    background:
      radial-gradient(ellipse at 20% 15%, #ffffff 0%, rgba(255,255,255,0) 45%),
      linear-gradient(170deg, var(--mist-light) 0%, var(--mist-mid) 60%, var(--mist-deep) 100%);
  }
  .back-cover .brand-name { left: 0; right: 0; top: 112px; text-align: center; font-size: 26px; }
  .sample-label {
    position: absolute; left: 0; right: 0; top: 217px;
    text-align: center; color: var(--text-light);
    font-size: 15px; letter-spacing: 1.6px;
  }
  .stamp-field {
    position: absolute; left: 35px; top: 247px;
    width: 316px; height: 170px;
    background: #ffffff; border-radius: 7px;
  }

  /* Vorderseite */
  .front-cover .panel-media {
    background:
      radial-gradient(ellipse at 35% 45%, var(--bottle-violet) 0%, rgba(91,61,142,0) 45%),
      radial-gradient(ellipse at 80% 85%, var(--bottle-violet) 0%, rgba(91,61,142,0) 35%),
      linear-gradient(160deg, var(--mist-light) 0%, var(--mist-deep) 40%, var(--bottle-blue) 80%, #2b3a8e 100%);
  }
  .front-cover .brand-name { right: 16px; top: 52px; font-size: 25px; }

  /* Innenseiten */
  .inside-left .panel-media {
    background:
      radial-gradient(ellipse at 85% 35%, var(--nebula-pink) 0%, rgba(232,143,214,0) 30%),
      radial-gradient(ellipse at 60% 95%, var(--nebula-magenta) 0%, rgba(192,42,154,0) 45%),
      linear-gradient(160deg, var(--night) 0%, var(--nebula-violet) 55%, var(--nebula-magenta) 100%);
  }
  .inside-right .panel-media {
    background:
      radial-gradient(ellipse at 35% 35%, var(--nebula-glow) 0%, rgba(243,230,246,0) 35%),
      radial-gradient(ellipse at 70% 85%, var(--nebula-magenta) 0%, rgba(192,42,154,0) 50%),
      linear-gradient(170deg, var(--nebula-violet) 0%, var(--nebula-pink) 40%, var(--nebula-magenta) 100%);
  }
  .inside-message {
    position: absolute; left: 0; right: 0;
    text-align: center; text-transform: uppercase;
    font-size: 21px; line-height: 28.5px; letter-spacing: 1.6px;
  }
  .inside-left .inside-message { top: 60px; color: var(--text-light); }
  .inside-right .inside-message { top: 60px; color: var(--text-dark); }
  .inside-left .brand-name { left: 0; right: 0; top: 308px; text-align: center; font-size: 24px; }
</style>
</head>
<body>
  <main class="print-sheet">
    <section class="panel back-cover">
      <div class="panel-media" role="img" aria-label="Heller, lavendelfarbener Wasserhintergrund mit weichen Lichtreflexen"></div>
      <div class="brand-name">NaseNomade</div>
      <p class="sample-label">GRATISMUSTER</p>
      <div class="stamp-field"></div>
    </section>

    <section class="panel front-cover">
      <div class="panel-media" role="img" aria-label="Parfumflakons in Violett und Blau im Wasser liegend"></div>
      <div class="brand-name">NaseNomade</div>
    </section>

    <section class="panel inside-left">
      <div class="panel-media" role="img" aria-label="Dunkler Sternenhimmel mit violetten und pinken Nebeln und einem angedeuteten Arm"></div>
      <p class="inside-message">Lorem ipsum<br>dolor sit<br>amet<br>consectetuer<br>adipiscing<br>elit sed.</p>
      <div class="brand-name">NaseNomade</div>
    </section>

    <section class="panel inside-right">
      <div class="panel-media" role="img" aria-label="Leuchtender pinkfarbener Nebel mit zwei sich nähernden Händen"></div>
      <p class="inside-message">Dolor<br>sit amet.</p>
    </section>
  </main>
</body>
</html>
```